Boutique custom software development company needs new business card

Our nearly 20 year old custom software development company would like to better include the fact that we are now providing Bitcoin services. These new services are B2B include education (how to acquire and securely hold Bitcoin) and integrating Bitcoin payments into existing ecommerce sites or other existing systems. Please keep the card clean and simple. Attached is our current design and some other files. vextorial.com

Target Market(s)

businesses owners interested in long term relationship

Industry/Entity Type

Custom software development and Bitcoin

Contact Information for Business Card

Dale Parker, dale@vextorial.com, vextorial.com, (888) 555-VXTRL

Font styles to use
Other font styles liked:
• monospace

Requirements
Must have
• double-sided
Nice to have
• clean and simple
Should not have
• physical address

```html
<!DOCTYPE html>
<html lang="en">
<head>
<meta charset="UTF-8">
<title>Vextorial — Business Card</title>
<link href="https://fonts.googleapis.com/css2?family=Montserrat:wght@400;500;700;800&display=swap" rel="stylesheet">
<style>
  :root {
    --page-bg: #e4e4e4;
    --card-bg: #d8e2ee;
    --brand-blue: #3e74bd;
    --brand-orange: #f07c22;
    --ink: #3a3a3a;
    --shadow: rgba(0, 0, 0, 0.28);
  }
  * { box-sizing: border-box; margin: 0; padding: 0; }
  html, body {
    width: 1200px;
    height: 900px;
    overflow: hidden;
    background: var(--page-bg);
    font-family: "Montserrat", sans-serif;
  }
  .sheet {
    position: relative;
    width: 1200px;
    height: 900px;
  }
  .card {
    position: absolute;
    left: 250px;
    width: 700px;
    height: 400px;
    background: var(--card-bg);
    border-radius: 22px;
    overflow: hidden;
    box-shadow: 0 6px 16px var(--shadow);
  }
  .card--front { top: 35px; }
  .card--back { top: 465px; }

  /* Brand name block */
  .brand {
    display: flex;
    flex-direction: column;
    align-items: flex-start;
  }
  .brand__name {
    font-weight: 800;
    color: var(--brand-blue);
    letter-spacing: 0.02em;
    line-height: 1;
  }
  .brand__tagline {
    font-weight: 500;
    color: var(--brand-blue);
    line-height: 1.2;
    white-space: nowrap;
  }
  .brand__services {
    font-weight: 700;
    color: var(--brand-orange);
    line-height: 1.2;
    white-space: nowrap;
    letter-spacing: 0.04em;
  }

  .card--front .brand {
    position: absolute;
    left: 50%;
    top: 50%;
    transform: translate(-50%, -50%);
  }
  .card--front .brand__name { font-size: 72px; }
  .card--front .brand__tagline { font-size: 24px; margin-top: 6px; padding-left: 4px; }
  .card--front .brand__services { font-size: 16px; margin-top: 10px; padding-left: 4px; }

  .card--back .brand {
    position: absolute;
    left: 62px;
    top: 170px;
  }
  .card--back .brand__name { font-size: 42px; }
  .card--back .brand__tagline { font-size: 14px; margin-top: 4px; padding-left: 2px; }
  .card--back .brand__services { font-size: 10.5px; margin-top: 6px; padding-left: 2px; }

  .divider {
    position: absolute;
    left: 392px;
    top: 120px;
    width: 1.5px;
    height: 150px;
    background: var(--brand-orange);
  }

  .contact {
    position: absolute;
    left: 420px;
    top: 112px;
  }
  .contact__name {
    font-weight: 800;
    font-size: 25px;
    letter-spacing: 0.04em;
    line-height: 1;
    text-transform: uppercase;
    white-space: nowrap;
  }
  .contact__first { color: var(--brand-orange); }
  .contact__last { color: var(--brand-blue); }
  .contact__role {
    font-weight: 400;
    font-size: 15px;
    color: var(--ink);
    letter-spacing: 0.05em;
    margin-top: 4px;
  }
  .contact__list {
    list-style: none;
    margin-top: 18px;
  }
  .contact__item {
    display: flex;
    align-items: center;
    gap: 8px;
    font-size: 14.5px;
    color: var(--ink);
    letter-spacing: 0.05em;
    line-height: 1;
    margin-bottom: 10px;
    white-space: nowrap;
  }
  .contact__icon {
    width: 13px;
    height: 13px;
    flex: none;
  }

  .edge-band {
    position: absolute;
    left: 0;
    bottom: 0;
    width: 700px;
    height: 14px;
  }
</style>
</head>
<body>
  <main class="sheet">
    <section class="card card--front" aria-label="Card front">
      <div class="brand">
        <span class="brand__name">VEXTORIAL</span>
        <span class="brand__tagline">developer of custom applications</span>
        <span class="brand__services">BITCOIN EDUCATION &amp; PAYMENT INTEGRATION</span>
      </div>
    </section>

    <section class="card card--back" aria-label="Card back">
      <div class="brand">
        <span class="brand__name">VEXTORIAL</span>
        <span class="brand__tagline">developer of custom applications</span>
        <span class="brand__services">BITCOIN EDUCATION &amp; PAYMENT INTEGRATION</span>
      </div>

      <div class="divider"></div>

      <div class="contact">
        <p class="contact__name"><span class="contact__first">Dale</span> <span class="contact__last">Parker</span></p>
        <p class="contact__role">Owner</p>
        <ul class="contact__list">
          <li class="contact__item">
            <svg class="contact__icon" viewBox="0 0 16 16" aria-hidden="true">
              <path fill="var(--brand-blue)" d="M3.6 1.2l2.3 2.6-1.3 1.8c.8 1.8 2.1 3.2 3.8 4l1.8-1.3 2.6 2.3-1.3 2.4C6.9 13 3 9.1 1.2 4.5z"/>
            </svg>
            (888) 555-VXTRL
          </li>
          <li class="contact__item">
            <svg class="contact__icon" viewBox="0 0 16 16" aria-hidden="true">
              <rect x="1" y="3" width="14" height="10" rx="1" fill="var(--brand-blue)"/>
              <path d="M1.5 3.8L8 9l6.5-5.2" fill="none" stroke="var(--card-bg)" stroke-width="1.3"/>
            </svg>
            dale@vextorial.com
          </li>
          <li class="contact__item">
            <svg class="contact__icon" viewBox="0 0 16 16" aria-hidden="true">
              <circle cx="8" cy="8" r="7" fill="var(--brand-blue)"/>
              <path d="M1 8h14M8 1c-2.5 2.5-2.5 11.5 0 14M8 1c2.5 2.5 2.5 11.5 0 14" fill="none" stroke="var(--card-bg)" stroke-width="1"/>
            </svg>
            www.vextorial.com
          </li>
        </ul>
      </div>

      <svg class="edge-band" viewBox="0 0 700 14" preserveAspectRatio="none" aria-hidden="true">
        <polygon points="0,8 452,8 446,14 0,14" fill="var(--brand-blue)"/>
        <polygon points="458,3 700,0 700,14 450,14" fill="var(--brand-orange)"/>
      </svg>
    </section>
  </main>
</body>
</html>
```